New LLC consulting company needs a business card design

I need a business card design for new company in Alexandria Virginia called TK Verdane Consulting LLC. The company is focused on consulting for defense and national security issues with expertise in nuclear and space topics. I would like to see designs that are simple and I am open to colors except for brown.

Target Market(s)

All businesses that are seeking consulting help

Industry/Entity Type

Consulting

Contact Information for Business Card

Name of company - TK Verdane Consulting LLC; name (Delia Pratt) President; email: prattdq47@mailvessa.com; Phone: 703-555-0142

Requirements
Must have
• The details described above
Nice to have
• I'm open to all ideas
Should not have
• No brown

```html
<!DOCTYPE html>
<html lang="en">
<head>
<meta charset="utf-8">
<title>TK Verdane Consulting LLC — Business Card</title>
<link rel="stylesheet" href="https://fonts.googleapis.com/css2?family=Bodoni+Moda:wght@600&family=Cookie&family=Arimo:wght@400;500&display=swap">
<style>
  :root {
    --stage: #2b2b2b;
    --card-front: #1f3f4d;
    --card-back: #ffffff;
    --ink-white: #ffffff;
    --ink-blue: #1f6fc0;
    --ink-grey: #7a7a7a;
    --ink-dark: #2a2a2a;
    --logo-grey: #6e6e6e;
  }
  * { margin: 0; padding: 0; box-sizing: border-box; }
  html, body { width: 1200px; height: 800px; overflow: hidden; }
  body {
    background: var(--stage);
    display: flex;
    flex-direction: column;
    align-items: center;
    justify-content: center;
    gap: 44px;
  }
  .card {
    width: 580px;
    height: 330px;
    border-radius: 18px;
    position: relative;
    overflow: hidden;
  }
  .card--front { background: var(--card-front); }
  .card--back { background: var(--card-back); }

  .wordmark {
    font-family: "Bodoni Moda", Georgia, serif;
    font-weight: 600;
    line-height: 1;
  }
  .card--front .wordmark {
    position: absolute;
    left: 0; right: 0; top: 50%;
    transform: translateY(-50%);
    text-align: center;
    color: var(--ink-white);
  }
  .card--front .wordmark__name { display: block; font-size: 62px; letter-spacing: 1px; }
  .card--front .wordmark__sub { display: block; font-size: 18px; letter-spacing: 5px; margin-top: 14px; text-transform: uppercase; }

  .holder {
    position: absolute;
    left: 42px; top: 46px;
  }
  .holder__name {
    font-family: "Cookie", cursive;
    font-size: 52px;
    color: var(--ink-blue);
    line-height: 1;
  }
  .holder__title {
    font-family: "Arimo", Arial, sans-serif;
    font-size: 15px;
    letter-spacing: 1px;
    color: var(--ink-grey);
    margin-top: 4px;
  }

  .card--back .wordmark {
    position: absolute;
    right: 40px; top: 118px;
    color: var(--logo-grey);
    text-align: left;
  }
  .card--back .wordmark__name { display: block; font-size: 30px; }
  .card--back .wordmark__sub { display: block; font-size: 10px; letter-spacing: 2.5px; margin-top: 6px; text-transform: uppercase; }

  .contacts {
    position: absolute;
    left: 42px; right: 40px; bottom: 36px;
    display: flex;
    gap: 34px;
    font-family: "Arimo", Arial, sans-serif;
    font-size: 17px;
    color: var(--ink-dark);
  }
  .contacts__item { display: flex; align-items: center; gap: 8px; }
  .contacts__icon { width: 16px; height: 16px; fill: var(--ink-blue); }
</style>
</head>
<body>
  <section class="card card--front" aria-label="Card front">
    <div class="wordmark">
      <span class="wordmark__name">TK Verdane</span>
      <span class="wordmark__sub">Consulting LLC</span>
    </div>
  </section>

  <section class="card card--back" aria-label="Card back">
    <div class="holder">
      <p class="holder__name">Delia Pratt</p>
      <p class="holder__title">PRESIDENT</p>
    </div>

    <div class="wordmark">
      <span class="wordmark__name">TK Verdane</span>
      <span class="wordmark__sub">Consulting LLC</span>
    </div>

    <div class="contacts">
      <span class="contacts__item">
        <svg class="contacts__icon" viewBox="0 0 16 16" aria-hidden="true">
          <path d="M1 5c0-2 2-3 7-3s7 1 7 3v1h-3V4.5C11 4 9.5 4 8 4s-3 0-4 .5V6H1z"/>
          <path d="M3 8l2-2h6l2 2v6H3z"/>
          <circle cx="8" cy="10.5" r="1.8" fill="#fff"/>
        </svg>
        703-555-0142
      </span>
      <span class="contacts__item">
        <svg class="contacts__icon" viewBox="0 0 16 16" aria-hidden="true">
          <path d="M1 8L15 1 11 15 8 10z"/>
          <path d="M8 10l7-9-9 8z" fill="#fff" opacity=".5"/>
        </svg>
        prattdq47@mailvessa.com
      </span>
    </div>
  </section>
</body>
</html>
```